Brell Stone Company Business Cards

Front and Back Business Card - logo and text setup - cool design. I need workable photoshop or illustrator files so I can setup each employee card with design that is created
Updates

Hi everyone, thank you for the great entries. Please no more white and blue cards - there are so many already - black and silver only now please. thanks!

Target Market(s)

Construction Industry - Facility Managers

Industry/Entity Type

Construction

Contact Information for Business Card

I really like contemporary simplistic looks - clean neat....not opposed to seeing some black backrounds

Requirements
Must have
• Logo/website address with design on front only - www.brellstone-example.com (logo attached)
• Back:
• Name/Title/Company Address/Phone/email address
Nice to have
• Cool design
Should not have
• Nothing gimmicky like Fire or Water - since we are a Fire Protection company - it has all been done

```html
<!DOCTYPE html>
<html lang="en">
<head>
<meta charset="utf-8">
<title>Brell Stone Company Business Cards</title>
<link rel="stylesheet" href="https://fonts.googleapis.com/css2?family=Open+Sans:ital,wght@0,400;0,700;0,800;1,700&display=swap">
<style>
  :root {
    --backdrop: #2a2a2c;
    --card: #050505;
    --text: #f2f2f2;
    --muted: #bdbdbd;
    --rule: #6a6a6a;
    --accent-red: #f21f24;
    --accent-blue: #0d1f9c;
  }
  * { box-sizing: border-box; margin: 0; padding: 0; }
  html, body {
    width: 1200px;
    height: 960px;
    overflow: hidden;
    background: var(--backdrop);
    font-family: "Open Sans", Arial, sans-serif;
    color: var(--text);
  }
  .sheet {
    position: relative;
    width: 1200px;
    height: 960px;
  }
  .card {
    position: absolute;
    left: 250px;
    width: 700px;
    height: 400px;
    background: var(--card);
    overflow: hidden;
  }
  .card--front { top: 50px; }
  .card--back { top: 510px; }

  .brand {
    position: absolute;
    display: flex;
    align-items: center;
    gap: 14px;
  }
  .brand__mark {
    width: 22px;
    height: 22px;
    background: var(--accent-blue);
  }
  .brand__name {
    font-weight: 800;
    color: var(--accent-red);
    letter-spacing: -1px;
    line-height: 1;
    white-space: nowrap;
  }
  .card--front .brand {
    left: 0;
    right: 0;
    top: 140px;
    justify-content: center;
  }
  .card--front .brand__name { font-size: 72px; }
  .card--front .website {
    position: absolute;
    left: 0;
    right: 0;
    top: 255px;
    text-align: center;
    font-size: 19px;
    letter-spacing: 3px;
    color: var(--text);
  }

  .card--back .brand {
    right: 50px;
    top: 62px;
  }
  .card--back .brand__name { font-size: 50px; }
  .card--back .brand__mark { width: 16px; height: 16px; }

  .person {
    position: absolute;
    left: 50px;
    top: 150px;
  }
  .person__name {
    font-weight: 700;
    font-style: italic;
    font-size: 22px;
    line-height: 1.2;
  }
  .person__title {
    font-weight: 700;
    font-style: italic;
    font-size: 18px;
    color: var(--muted);
  }
  .divider {
    position: absolute;
    left: 260px;
    right: 0;
    top: 205px;
    height: 2px;
    background: var(--rule);
  }
  .contact {
    position: absolute;
    left: 50px;
    top: 232px;
    list-style: none;
  }
  .contact__item {
    display: flex;
    align-items: center;
    gap: 12px;
    font-size: 17px;
    line-height: 32px;
  }
  .contact__icon { width: 16px; height: 16px; flex: none; }
  .address {
    position: absolute;
    left: 330px;
    top: 268px;
    padding-left: 20px;
    border-left: 1px solid var(--rule);
    font-size: 18px;
    line-height: 30px;
  }
  .band {
    position: absolute;
    left: 0;
    right: 0;
    bottom: 0;
    height: 16px;
    background: var(--accent-blue);
  }
</style>
</head>
<body>
<main class="sheet">
  <section class="card card--front" aria-label="Business card front">
    <div class="brand">
      <span class="brand__mark"></span>
      <span class="brand__name">Brell Stone</span>
    </div>
    <p class="website">www.brellstone-example.com</p>
  </section>

  <section class="card card--back" aria-label="Business card back">
    <div class="brand">
      <span class="brand__mark"></span>
      <span class="brand__name">Brell Stone</span>
    </div>
    <div class="person">
      <p class="person__name">Dana Whitfield</p>
      <p class="person__title">President</p>
    </div>
    <div class="divider"></div>
    <ul class="contact">
      <li class="contact__item">
        <svg class="contact__icon" viewBox="0 0 16 16" aria-hidden="true"><path fill="#f21f24" d="M3.5 1.5l2.5 0 1 3.5-1.7 1.2a8 8 0 0 0 4.5 4.5L11 9l3.5 1v2.5c0 1-1 2-2 2C6.5 14.5 1.5 9.5 1.5 3.5c0-1 1-2 2-2z"/></svg>
        <span>(555) 014-2730</span>
      </li>
      <li class="contact__item">
        <svg class="contact__icon" viewBox="0 0 16 16" aria-hidden="true"><rect x="1" y="3" width="14" height="10" fill="#f21f24"/><path d="M1 3l7 6 7-6" fill="none" stroke="#050505" stroke-width="1.4"/></svg>
        <span>info@brellstone-example.com</span>
      </li>
      <li class="contact__item">
        <svg class="contact__icon" viewBox="0 0 16 16" aria-hidden="true"><g fill="none" stroke="#f21f24" stroke-width="1.4"><circle cx="8" cy="8" r="6.5"/><ellipse cx="8" cy="8" rx="3" ry="6.5"/><path d="M1.5 8h13M2.5 5h11M2.5 11h11"/></g></svg>
        <span>www.brellstone-example.com</span>
      </li>
    </ul>
    <address class="address" style="font-style: normal;">
      48 Harbor Point Road<br>
      Lakeview, NY 10000
    </address>
    <div class="band"></div>
  </section>
</main>
</body>
</html>
```